Popup Nightclub Grand Opening Flyer

We need to design a flyer for the grand opening of an upscale, exclusive nightclub called "Lantern". The design needs to be chic and exclusive. The background should be black and the text should primarily be white. We like minimalist designs.

Here is the text for the flyer
-
Velvetroll Atlanta Presents

Lantern (LOGO)

A Popup Nightclub Experience
For one night Only

Friday, October 18, 2013
Party begins at 9PM

INVITE ONLY

See invitation for location details
(Velvetroll Atlanta logo)

-
Examples we like

http://cdn4-x.pressfolio-example.com/sites/default/files/styles/image_content_width/hash/3b/fd/2468013579_4421_flyer.jpg?itok=K9rtQw2z

http://files.hubspace-example.net/files/8Hqq-Tr72WWE3kaRbTmcxP5QZK2F396J8nbRw4CKMHfdX2Y7qSEF-MqjxDoNrLY3QCyQJD7npjGaRq3k-Mhx6hqf3MDSWf8r3/2zenSaturdays.jpg

http://morvex-example.com/wp-content/uploads/siteskin/widgetkit/gallery/2zen/2zen-gen_qstay4-01.jpg

Hi All, one thing that we are seeing that we don't like is on over emphasis on the phrase "a popup nightclub experience" please don't make this the largest thing on the flyer

Target Market(s)

Target market is 25-35 year olds who are affluent (rich) and like luxury brands

Requirements
Must have
• Dark Background
Nice to have
• Velvetroll Logo on the bottom
Modern text that isn't curvy
Should not have
• Curved text

```html
<!DOCTYPE html>
<html lang="en">
<head>
<meta charset="utf-8">
<title>Lantern Nightclub — Popup Night Flyer</title>
<link rel="stylesheet" href="https://fonts.googleapis.com/css2?family=Jost:wght@300;400;600&display=swap">
<style>
  :root {
    --night: #000000;
    --ice: #e3ecf7;
    --ice-glow: rgba(150, 195, 255, 0.65);
    --ember-red: rgba(150, 28, 20, 0.85);
    --ember-orange: rgba(205, 115, 45, 0.75);
    --ember-gold: rgba(230, 190, 110, 0.45);
  }
  html, body {
    margin: 0;
    padding: 0;
    width: 1200px;
    height: 1080px;
    overflow: hidden;
    background: var(--night);
  }
  .flyer {
    position: relative;
    width: 1200px;
    height: 1080px;
    background: var(--night);
    font-family: "Jost", "Futura", sans-serif;
    color: var(--ice);
    text-transform: uppercase;
    overflow: hidden;
  }
  .ambient-lights {
    position: absolute;
    left: 110px;
    top: 250px;
    width: 980px;
    height: 800px;
    border-radius: 50%;
    background:
      radial-gradient(ellipse 40% 30% at 45% 35%, var(--ember-gold), transparent 70%),
      radial-gradient(ellipse 45% 35% at 55% 45%, var(--ember-orange), transparent 75%),
      radial-gradient(ellipse 50% 45% at 50% 55%, var(--ember-red), transparent 80%);
    filter: blur(8px);
  }
  .glow {
    text-shadow: 0 0 8px var(--ice-glow), 0 0 18px var(--ice-glow);
  }
  .line {
    position: absolute;
    left: 0;
    width: 1200px;
    text-align: center;
    margin: 0;
    line-height: 1;
  }
  .presenter {
    top: 26px;
    font-size: 24px;
    font-weight: 600;
    letter-spacing: 2.5px;
  }
  .brand-mark {
    position: absolute;
    left: 543px;
    top: 80px;
    width: 114px;
    height: 114px;
  }
  .brand-name {
    top: 352px;
    font-size: 54px;
    font-weight: 300;
    letter-spacing: 9px;
  }
  .brand-sub {
    top: 420px;
    font-size: 27px;
    font-weight: 300;
    letter-spacing: 4px;
  }
  .headline {
    font-size: 39px;
    font-weight: 600;
    letter-spacing: 1.5px;
  }
  .headline-1 { top: 516px; }
  .headline-2 { top: 570px; }
  .rule {
    position: absolute;
    height: 2px;
    background: var(--ice);
    box-shadow: 0 0 6px var(--ice-glow);
  }
  .rule-main { left: 318px; top: 626px; width: 528px; }
  .date {
    top: 657px;
    font-size: 37px;
    font-weight: 400;
    letter-spacing: 1px;
  }
  .time {
    top: 701px;
    font-size: 35px;
    font-weight: 600;
    letter-spacing: 1.5px;
  }
  .access {
    top: 778px;
    font-size: 35px;
    font-weight: 600;
    letter-spacing: 1.5px;
  }
  .rule-left { left: 360px; top: 796px; width: 92px; }
  .rule-right { left: 740px; top: 796px; width: 104px; }
  .location {
    top: 876px;
    font-size: 24px;
    font-weight: 600;
    letter-spacing: 2.5px;
  }
  .host {
    position: absolute;
    left: 0;
    top: 946px;
    width: 1200px;
    display: flex;
    justify-content: center;
    align-items: center;
    gap: 16px;
  }
  .host-dot {
    width: 34px;
    height: 34px;
    border-radius: 50%;
    background: var(--ice);
  }
  .host-name {
    font-size: 34px;
    font-weight: 400;
    letter-spacing: 3px;
    color: var(--ice);
  }
</style>
</head>
<body>
  <main class="flyer">
    <div class="ambient-lights" role="img" aria-label="Soft red, orange and gold bokeh light circles with faint swirling flourishes"></div>

    <p class="line presenter glow">Velvetroll Atlanta Presents</p>

    <svg class="brand-mark" viewBox="0 0 114 114" aria-hidden="true">
      <circle cx="57" cy="57" r="50" fill="none" stroke="#e3ecf7" stroke-width="10"/>
    </svg>
    <p class="line brand-name">Lantern</p>
    <p class="line brand-sub">Nightclub</p>

    <p class="line headline headline-1 glow">A Popup Nightclub Experience</p>
    <p class="line headline headline-2 glow">For One Night Only</p>
    <div class="rule rule-main"></div>

    <p class="line date glow">Friday, October 18, 2013</p>
    <p class="line time glow">Party Begins at 9PM</p>

    <div class="rule rule-left"></div>
    <p class="line access glow">Invite Only</p>
    <div class="rule rule-right"></div>

    <p class="line location glow">See Invitation for Location Details</p>

    <div class="host">
      <span class="host-dot" aria-hidden="true"></span>
      <span class="host-name">VELVETROLL ATLANTA</span>
    </div>
  </main>
</body>
</html>
```